Detail Shop Business card design

i need a business card design for my new detailing company called 'Brisk's Polish Works'. i want an all black and white design . simple, direct and to the point. i want the designer to choose a fitting font to match the logothe front should have logo, address, phone and email and the back side should have a slogan and text indicating that we offer services on anything including cars, trucks, motorcycles and RVs. slogan will read "we take pride in your ride"
maybe also very small on the back side the IG icon with Brisks_Polish_Works

phone 208.417.6352
address 3847 E Larkin Ave
Spokane WA 99214
email: BrisksPolish@mailvexo.com

Target Market(s)

all ages , auto enthusiasts

Industry/Entity Type

Automotive

Contact Information for Business Card

the front should have logo, address, phone and email and the back side should have a slogan and text indicating that we offer services on anything including cars, trucks, motorcycles and RVs. slogan will read "we take pride in your ride"

phone 208.417.6352
address 3847 E Larkin Ave
Spokane WA 99214

Colors
000000
ffffff

Requirements
Must have
• bold font and very simple design with good spacing
Nice to have
• anything creative from the designer indicating we service any types of vehicles
Should not have
• any colors ,

```html
<!DOCTYPE html>
<html lang="en">
<head>
<meta charset="utf-8">
<title>Brisk's Polish Works — Business Card</title>
<link rel="stylesheet" href="https://fonts.googleapis.com/css2?family=Source+Sans+3:wght@400;600;700&display=swap">
<style>
  :root {
    --backdrop: #4a423e;
    --card: #141414;
    --ink: #ffffff;
    --ink-soft: #bdbdbd;
    --mark: #a9a9a9;
  }
  html, body {
    margin: 0;
    padding: 0;
    width: 1200px;
    height: 864px;
    overflow: hidden;
    background: var(--backdrop);
    font-family: "Source Sans 3", "Myriad Pro", Arial, sans-serif;
  }
  .canvas {
    position: relative;
    width: 1200px;
    height: 864px;
  }
  .card {
    position: absolute;
    width: 525px;
    height: 300px;
    background: var(--card);
    border-radius: 3px;
    box-shadow: 0 10px 28px rgba(0,0,0,0.45);
    box-sizing: border-box;
  }
  .card--brand { left: 50px; top: 140px; }
  .card--contact { left: 625px; top: 424px; }

  /* Brand side */
  .brand {
    position: absolute;
    left: 0; right: 0; top: 46px;
    display: flex;
    flex-direction: column;
    align-items: center;
  }
  .brand__mark {
    width: 22px; height: 22px;
    border-radius: 50%;
    background: var(--mark);
    margin-bottom: 12px;
  }
  .brand__name {
    color: var(--mark);
    font-weight: 700;
    font-size: 30px;
    letter-spacing: 0.5px;
    margin: 0;
  }
  .slogan {
    position: absolute;
    left: 0; right: 0; top: 170px;
    text-align: center;
    color: var(--ink);
    font-weight: 700;
    font-size: 21px;
    letter-spacing: 0.5px;
    margin: 0;
  }
  .slogan-rule {
    position: absolute;
    left: 110px; right: 110px; top: 202px;
    height: 1px;
    background: var(--ink-soft);
  }
  .services {
    position: absolute;
    left: 0; right: 0; top: 212px;
    text-align: center;
    color: var(--ink-soft);
    font-size: 14px;
    margin: 0;
  }

  /* Contact side */
  .contact {
    position: absolute;
    left: 150px; top: 66px;
    color: var(--ink);
    text-align: center;
    width: 240px;
  }
  .contact__name {
    font-weight: 700;
    font-size: 20px;
    letter-spacing: 0.5px;
    margin: 0;
    line-height: 1.1;
  }
  .contact__role {
    font-size: 14px;
    letter-spacing: 0.5px;
    margin: 0 0 10px;
  }
  .contact__lines {
    list-style: none;
    margin: 0;
    padding: 0;
    font-size: 15px;
    line-height: 1.32;
  }
</style>
</head>
<body>
<main class="canvas">
  <section class="card card--brand" aria-label="Brand side">
    <div class="brand">
      <span class="brand__mark" aria-hidden="true"></span>
      <h1 class="brand__name">Brisk's Polish Works</h1>
    </div>
    <p class="slogan">WE TAKE PRIDE IN YOUR RIDE</p>
    <div class="slogan-rule" aria-hidden="true"></div>
    <p class="services">we offer services on anything including cars, trucks, motorcycles &amp; RVs</p>
  </section>

  <section class="card card--contact" aria-label="Contact side">
    <div class="contact">
      <h2 class="contact__name">MARCUS HALE</h2>
      <p class="contact__role">PRESIDENT</p>
      <ul class="contact__lines">
        <li>3847 E Larkin Ave</li>
        <li>Spokane WA 99214</li>
        <li>(P) 208.417.6352</li>
        <li>(M) 836 512 7408</li>
        <li>BrisksPolish@mailvexo.com</li>
        <li>www.briskspolishworks.com</li>
      </ul>
    </div>
  </section>
</main>
</body>
</html>
```